2 page Web Site Design (Coded), simple, not picky

I need a web portal for a PPC marketing business. I have the logo, some imagery, and some websites to base the design on.

***Background***
The name of the business is "Quiet Harbor Outreach Partners" or QHOP. We provide listings in a searchable database for Dental Sleep Medicine doctors. These are doctors who treat snoring/sleep apnea/and CPAP users with oral appliances. Client doctors will have their own "landing page website" where PPC prospects land from the PPC campaigns. Logos for supporting/landing page websites have been uploaded.
***End Background***

THIS website (for you to design) is to introduce doctors to the concept and detail the services. i.e. PPC campaign management services, listing on a national database of Dental Sleep Medicine practitioners, and a fully featured website dedicated to Snoring, Sleep Apnea, and CPAP Alternative treatment (those websites are "Farewell-Rumble.com", "Farewell-NightGasp.com", and ""Farewell-MaskTube.com")

SEM websites whose look I enjoy are:

http://www.brightlorn.example/marketing-services/pay-per-click/

http://www.parcelwindow.example/welcome/pay-per-click-services/

http://www.tessaroqco.example/marketing-services/paid-search-management/

The main colors are Red, White, & Blue. Red and blue used mostly for accents/emphasis.

The main/index page's purpose is to, as best possible, convey the idea of SEM campaign management with supporting websites being their best option for internet marketing!
The secondary page is just a slightly modified layout where details can be explained.

Target Market(s)

Dentists who practice Dental Sleep Medicine (see www.ovrqx.example)

Industry/Entity Type

Marketing

Requirements
Must have
• -Sign-up form for the generation of leads... Simple script that sends E-mail is fine... Doctor's Name, Business Name, Business Address, E-mail address, phone #.

-Graphics that will clearly describe the services being provided.

```html
<!DOCTYPE html>
<html lang="en">
<head>
<meta charset="utf-8">
<title>Quiet Harbor Outreach Partners</title>
<link href="https://fonts.googleapis.com/css2?family=Roboto+Condensed:wght@400;700&family=Arimo:wght@400;700&display=swap" rel="stylesheet">
<style>
:root{
  --red:#b3242c;
  --red-dark:#8e1a20;
  --blue:#173a82;
  --blue-dark:#122e6a;
  --blue-light:#2a5ca8;
  --ink:#333;
  --page:#ececec;
  --line:#dcdcdc;
}
*{box-sizing:border-box;margin:0;padding:0}
html,body{width:1063px;height:1200px;overflow:hidden}
body{position:relative;background:var(--page);font-family:"Arimo",Arial,sans-serif;color:var(--ink)}
.abs{position:absolute}
.header{left:0;top:0;width:1063px;height:80px;background:linear-gradient(#fff,#f3f3f3)}
.brand{left:140px;top:9px;width:227px;height:129px;background:linear-gradient(#fff,#ececec);border-radius:0 0 8px 8px;box-shadow:0 2px 6px rgba(0,0,0,.25);z-index:3}
.brand-mark{left:24px;top:40px;width:30px;height:30px;border-radius:50%;background:var(--blue)}
.brand-name{left:62px;top:34px;font:700 34px "Arimo",Arial,sans-serif;color:var(--red);line-height:1}
.brand-sub{left:25px;top:78px;font:700 10.5px "Arimo",Arial,sans-serif;color:var(--red)}
.nav a{position:absolute;top:33px;font-size:13px;color:var(--blue);text-decoration:none}
.nav .active{left:520px;top:27px;width:98px;height:25px;border-radius:13px;background:linear-gradient(#3f6fc0,var(--blue-dark));color:#fff;text-align:center;line-height:25px;box-shadow:0 0 0 2px #c8d3e8}
.hero{left:0;top:80px;width:1063px;height:381px;background:linear-gradient(100deg,#5b5d66 0%,#8a8f9a 25%,#c9a38a 45%,#d8cfc8 60%,#7d7f86 80%,#4e5058 100%)}
.hero-panel{left:396px;top:198px;width:546px;height:245px;background:rgba(255,255,255,.86);border:1px solid rgba(255,255,255,.9);border-radius:3px}
.bars{right:14px;bottom:0}
.hero-lead{left:32px;top:29px;width:480px;font-size:15.5px;line-height:20px;color:var(--blue-light)}
.hero-list{list-style:none;left:38px;top:91px;width:490px}
.hero-list li{position:relative;font-size:10.8px;line-height:12.5px;color:#222;margin-bottom:19px}
.hero-list li:nth-child(3){margin-bottom:19px}
.hero-list svg{position:absolute;left:-16px;top:1px}
.sem-box{left:120px;top:184px;width:275px;height:313px;background:linear-gradient(#c22c35,var(--red-dark));border-radius:3px;box-shadow:0 0 0 2px rgba(255,255,255,.6);color:#fff;z-index:2}
.sem-box h2{position:absolute;left:0;top:12px;width:100%;text-align:center;font:400 21px "Roboto Condensed",sans-serif}
.sem-box .sub{position:absolute;left:0;top:36px;width:100%;text-align:center;font-size:12px}
.sem-box .rule{position:absolute;left:0;top:65px;width:100%;height:1px;background:rgba(255,255,255,.25)}
.sem-box p{position:absolute;left:14px;top:76px;width:246px;font-size:10.5px;line-height:12.6px}
.sem-box ul{position:absolute;left:41px;top:154px;width:220px;list-style:none;font-size:10.5px;line-height:12.6px}
.sem-box li{position:relative;margin-bottom:12px}
.sem-box li::before{content:"";position:absolute;left:-15px;top:4px;border-left:4px solid #fff;border-top:2.5px solid transparent;border-bottom:2.5px solid transparent}
.btn-more{left:171px;top:276px;width:88px;height:22px;border-radius:11px;background:linear-gradient(#4f7fce,var(--blue-dark));box-shadow:0 0 0 1px #fff;font-size:13px;text-align:center;line-height:22px}
.shadow{height:10px;border-radius:50%;background:radial-gradient(ellipse at center,rgba(0,0,0,.18),rgba(0,0,0,0) 70%)}
.card{left:106px;top:484px;width:850px;height:660px;background:#fff;border:1px solid var(--line);border-radius:4px}
.welcome{left:129px;top:536px;font:400 21px "Roboto Condensed",sans-serif;color:#222}
.hr{left:127px;top:572px;width:512px;height:1px;background:var(--line)}
.body-text{font-size:11px;line-height:16px;color:#444;width:512px;left:127px}
.sub-head{left:127px;font:700 16px "Arimo",Arial,sans-serif;color:var(--blue)}
.shot{top:729px;width:251px;height:228px;border:1px solid #bbb;background:linear-gradient(#f5f6fa,#e6e9f1)}
.red-list{left:127px;top:1061px;list-style:none;font-size:11px;line-height:16px;color:#444}
.red-list li{position:relative;padding-left:12px}
.red-list li::before{content:"";position:absolute;left:0;top:5px;border-left:4px solid var(--red);border-top:2.5px solid transparent;border-bottom:2.5px solid transparent}
.read-more{left:127px;top:1110px;font-size:10px;font-weight:700;color:var(--blue)}
.ppc-box{left:659px;top:531px;width:274px;height:259px;background:linear-gradient(var(--blue),var(--blue-dark));border-radius:3px;color:#fff}
.ppc-box h2{position:absolute;left:0;top:13px;width:100%;text-align:center;font:400 21px "Roboto Condensed",sans-serif}
.ppc-box .sub{position:absolute;left:0;top:40px;width:100%;text-align:center;font-size:11px}
.ppc-box .rule{position:absolute;left:0;top:67px;width:100%;height:1px;background:rgba(255,255,255,.2)}
.ppc-box ul{position:absolute;left:39px;top:80px;width:215px;list-style:none;font-size:9.8px;line-height:11.6px}
.ppc-box li{position:relative;margin-bottom:13px}
.ppc-box li::before{content:"";position:absolute;left:-14px;top:3px;border-left:4px solid #fff;border-top:2.5px solid transparent;border-bottom:2.5px solid transparent}
.signup{left:659px;top:813px;width:274px;height:285px;background:#fff;border:1px solid var(--line);border-radius:3px}
.signup h2{position:absolute;left:0;top:13px;width:100%;text-align:center;font:400 20px "Roboto Condensed",sans-serif;color:#222}
.signup .rule{position:absolute;left:0;top:53px;width:100%;height:1px;background:var(--line)}
.signup label{position:absolute;left:18px;font-size:11px;color:#333}
.signup .field{position:absolute;left:125px;width:134px;height:18px;border:1px solid #bbb;border-radius:3px;background:linear-gradient(#d6d6d6,#f1f1f1)}
.submit{position:absolute;left:125px;top:247px;width:82px;height:23px;border-radius:12px;background:linear-gradient(#d63a41,var(--red-dark));color:#fff;font-size:12.5px;text-align:center;line-height:23px;box-shadow:0 0 0 1px #e6a0a3}
.footer{left:108px;top:1160px;font-size:9px;line-height:11px;color:#555}
</style>
</head>
<body>
<div class="abs header"></div>
<div class="abs hero" role="img" aria-label="Photo of a peaceful sleeper resting on a pillow"></div>

<div class="abs brand">
  <span class="abs brand-mark"></span>
  <span class="abs brand-name">QHOP</span>
  <span class="abs brand-sub">Quiet Harbor Outreach Partners</span>
</div>

<nav class="nav">
  <a class="active" href="#">Landing Page</a>
  <a href="#" style="left:684px">About</a>
  <a href="#" style="left:793px">Services</a>
  <a href="#" style="left:899px">Contact</a>
</nav>

<section class="abs hero-panel">
  <svg class="abs bars" width="150" height="160" viewBox="0 0 150 160">
    <g fill="#fff" opacity=".55">
      <rect x="0" y="120" width="20" height="40"/>
      <rect x="27" y="95" width="20" height="65"/>
      <rect x="54" y="60" width="20" height="100"/>
      <rect x="81" y="30" width="20" height="130"/>
      <rect x="108" y="0" width="40" height="160"/>
    </g>
  </svg>
  <p class="abs hero-lead">Each participant has a customized “landing page” on a website that exclusively promotes the OSB therapies and OSB therapists.</p>
  <ul class="abs hero-list">
    <li><svg width="8" height="8" viewBox="0 0 8 8"><path d="M7 1 2 6M2 2v4h4" stroke="#b3242c" stroke-width="1.6" fill="none"/></svg>We set up and manage your search engine marketing campaigns for you.</li>
    <li><svg width="8" height="8" viewBox="0 0 8 8"><path d="M7 1 2 6M2 2v4h4" stroke="#b3242c" stroke-width="1.6" fill="none"/></svg>You only pay when visitors click on your ad and visit your website.</li>
    <li><svg width="8" height="8" viewBox="0 0 8 8"><path d="M7 1 2 6M2 2v4h4" stroke="#b3242c" stroke-width="1.6" fill="none"/></svg>We design your ad campaign to optimize ad click conversion rates.</li>
    <li><svg width="8" height="8" viewBox="0 0 8 8"><path d="M7 1 2 6M2 2v4h4" stroke="#b3242c" stroke-width="1.6" fill="none"/></svg>We send you regular advertising effectiveness monitoring, and analysis reports so you can determine your return-on-investment and adjust your budget accordingly.</li>
  </ul>
</section>

<div class="abs card"></div>

<section class="abs sem-box">
  <h2>Search Engine Marketing</h2>
  <div class="sub">Online marketing strategy</div>
  <div class="rule"></div>
  <p>Search engine marketing is an online marketing strategy that aims to increase qualified visitor traffic to your website by positioning your advertisements at the top and right side of “natural” and “organic” search result pages</p>
  <ul>
    <li>You only pay when someone clicks on one of your advertisements.</li>
    <li>It is estimated that pay per click ads receive around 30% of all clicks on search engines.</li>
    <li>Seekora Ads, Lumino Search Marketing and Vantix AdHub are pay per click advertising platforms.</li>
  </ul>
  <div class="abs btn-more">More</div>
</section>
<div class="abs shadow" style="left:146px;top:500px;width:222px"></div>

<h1 class="abs welcome">Welcome to Quiet Harbor Outreach Partners</h1>
<div class="abs hr"></div>
<p class="abs body-text" style="top:583px">will drive customers to your practice with PPC Search engine Marketing and then educate them about the unique benefits inherent to OAT therapy with a dedicated website .</p>
<h2 class="abs sub-head" style="top:632px">What is Search Engine Marketing?</h2>
<p class="abs body-text" style="top:666px">Search engine marketing is an online marketing strategy that aims to increase qualified visitor traffic to your website by positioning your advertisements at the top and right side of “natural” and “organic” search result pages [descriptions below].</p>
<div class="abs shot" style="left:127px" role="img" aria-label="Screenshot of a search results page highlighting pay per click advertising"></div>
<div class="abs shot" style="left:389px" role="img" aria-label="Screenshot of a search results page highlighting natural search results"></div>
<h2 class="abs sub-head" style="top:980px">Search Engine Marketing(Pay Per Click)</h2>
<p class="abs body-text" style="top:1013px">Paid search results, called “Pay Per Click” (PPC) advertising, promote websites in “Sponsored” section of search results.</p>
<ul class="abs red-list">
  <li>You only pay when someone clicks on one of your advertisements.</li>
  <li>It is estimated that pay per click ads receive around 30% of all clicks on search engines.</li>
  <li>Seekora Ads, Lumino Search Marketing and Vantix AdHub are pay per click advertising platforms.</li>
</ul>
<a class="abs read-more">Read More...</a>

<section class="abs ppc-box">
  <h2>Pay Per Click</h2>
  <div class="sub">Search Engine Marketing Campaign Managment.</div>
  <div class="rule"></div>
  <ul>
    <li>We set up and manage your search engine marketing campaigns for you.</li>
    <li>You only pay when visitors click on your ad and visit your website.</li>
    <li>We design your ad campaign to optimize ad click conversion rates.</li>
    <li>We send you regular advertising effectiveness monitoring, and analysis reports so you can determine your return-on-investment and adjust your budget accordingly.</li>
  </ul>
</section>
<div class="abs shadow" style="left:670px;top:790px;width:250px"></div>

<form class="abs signup">
  <h2>Signup Today!</h2>
  <div class="rule"></div>
  <label style="top:73px">Doctor's Name</label><span class="field" style="top:70px"></span>
  <label style="top:100px">Business Name</label><span class="field" style="top:97px"></span>
  <label style="top:128px">Business Address</label><span class="field" style="top:123px;height:57px"></span>
  <label style="top:191px;left:22px">E-mail address</label><span class="field" style="top:188px"></span>
  <label style="top:218px">Phone.No</label><span class="field" style="top:215px"></span>
  <div class="submit">Submit</div>
</form>
<div class="abs shadow" style="left:680px;top:1095px;width:230px"></div>

<footer class="abs footer">Copyrights@Quiet Harbor Outreach Partners.com<br>All rights reserved.</footer>
</body>
</html>
```